Law Firm Logo and Business Card Design

I need a logo and business card design for a law firm I just started. The law firm is named Law Office of Doreen K. Ashworth, LLC. The type of law I practice is Family Law, which includes divorce, custody, child support, alimony, property division, and the like. I would like to see designs that are unique and modern, yet sophisticated. I would also like to use the logo/design for my letterhead. I am not opposed to using some form of the scales of justice although I'd like something other than the typical, old fashioned scales of justice. I had considered a house made out of puzzle pieces with one puzzle piece pulled away from the others, with the logo text reading "Putting your life back together, one piece at a time." However, I don't want that particular design to look juvenile. I also would not be opposed to some form of my initials on the logo -- my initials are DKA. I am open to any other ideas you may have. I would like to see raised designs/lettering, and/or metallic finish. I like the colors black, white, gold, silver, and/or teal.

Industry/Entity Type

Law Firm

```html
<!DOCTYPE html>
<html lang="en">
<head>
<meta charset="utf-8">
<title>Law Office of Doreen K. Ashworth, LLC — Business Card</title>
<link rel="stylesheet" href="https://fonts.googleapis.com/css2?family=Noto+Sans:wght@400;700&display=swap">
<style>
  :root {
    --page: #ffffff;
    --frame: #1c1c1b;
    --card: #d9d9d9;
    --ink: #1c1c1b;
    --accent: #e8821e;
    --band: #1c1c1b;
    --motif: #c4c4c4;
  }
  * { margin: 0; padding: 0; box-sizing: border-box; }
  html, body { width: 1200px; height: 750px; overflow: hidden; background: var(--page); }
  .canvas {
    position: relative; width: 1200px; height: 750px;
    border: 2px solid var(--frame); background: var(--page);
    font-family: "Noto Sans", sans-serif; color: var(--ink);
  }
  .card {
    position: absolute; left: 62px; top: 66px; width: 1075px; height: 618px;
    background: var(--card); overflow: hidden;
  }
  .motif {
    position: absolute; left: 565px; top: 40px; width: 510px; height: 420px;
    border-radius: 48% 52% 45% 55% / 50% 50% 50% 50%;
    background: radial-gradient(ellipse at 45% 45%, var(--motif) 0%, rgba(196,196,196,0.6) 60%, rgba(217,217,217,0) 78%);
  }
  .firm-name {
    position: absolute; left: 80px; top: 220px;
    font-size: 44px; font-weight: 700; line-height: 49px; letter-spacing: 0.2px;
  }
  .rule {
    position: absolute; left: 77px; top: 342px; width: 862px; height: 2px; background: var(--ink);
  }
  .address {
    position: absolute; left: 80px; top: 368px;
    font-size: 28px; line-height: 39px; font-weight: 400;
  }
  .contacts { position: absolute; left: 490px; top: 366px; list-style: none; }
  .contacts li {
    display: flex; align-items: center; height: 49px;
    font-size: 28px; font-weight: 400;
  }
  .contacts svg { width: 34px; height: 34px; margin-right: 14px; flex: none; }
  .accent-line {
    position: absolute; left: 0; top: 524px; width: 100%; height: 4px; background: var(--accent);
  }
  .band {
    position: absolute; left: 0; top: 532px; width: 100%; height: 86px; background: var(--band);
  }
</style>
</head>
<body>
<div class="canvas">
  <div class="card">
    <div class="motif" role="img" aria-label="Faint globe made of interlocking puzzle pieces, one piece pulled away"></div>

    <h1 class="firm-name">Law Office of<br>Doreen K. Ashworth, LLC.</h1>
    <div class="rule"></div>

    <address class="address" style="font-style:normal">
      2750 Harbor Point Blvd.<br>
      Suite 410<br>
      Annapolis, MD 21403
    </address>

    <ul class="contacts">
      <li>
        <svg viewBox="0 0 34 34" aria-hidden="true">
          <rect width="34" height="34" rx="6" fill="#1c1c1b"/>
          <path d="M12 8c1 0 3 4 3 5s-2 1.5-2 2.5 3 5 4 5.5 1.5-1.5 2.5-1.5 4.5 2 4.5 3-2 4-4 4C14 27 8 18 8 12c0-2 3-4 4-4z" fill="#fff"/>
        </svg>
        +443-555-0172
      </li>
      <li>
        <svg viewBox="0 0 34 34" aria-hidden="true">
          <rect width="34" height="34" rx="6" fill="#1c1c1b"/>
          <rect x="5" y="9" width="24" height="16" fill="#fff"/>
          <path d="M5 9l12 9 12-9M5 25l9-8M29 25l-9-8" fill="none" stroke="#1c1c1b" stroke-width="1.6"/>
        </svg>
        doreen@ashworthfamilylaw.com
      </li>
      <li>
        <svg viewBox="0 0 34 34" aria-hidden="true">
          <rect width="34" height="34" rx="6" fill="#1c1c1b"/>
          <g fill="none" stroke="#fff" stroke-width="1.6">
            <circle cx="17" cy="17" r="10"/>
            <ellipse cx="17" cy="17" rx="4.5" ry="10"/>
            <path d="M7 17h20M9 12h16M9 22h16"/>
          </g>
        </svg>
        www.ashworthfamilylaw.com
      </li>
    </ul>

    <div class="accent-line"></div>
    <div class="band"></div>
  </div>
</div>
</body>
</html>
```